A Label for an ECO Friendly Spirit Company

Design a label which can be used for vodka and gin (London Dry Gin). It should be Square type Like the Shape File you see in the uploads. KIRO means Kind Inventive Rare and Original. We want a cool and slim label that calls for eco-friendly. We want to use it for our premium
Vodka and our London Dry Gin. Please use the logo and design it in Square Type.

40%vol, 700ml

Target Market(s)

spirits and events

Industry/Entity Type

SPIRITS

Colors
00AB8E
00BBA5
67D7C9
C6EFE9
E9F9F6
59FF00
82FF00
B8FF75
E3FFCB
F4FFEA

Requirements
Must have
• Logo from KIRO, Squaee Shape

```html
<!DOCTYPE html>
<html lang="en">
<head>
<meta charset="utf-8">
<title>KIRO London Dry Gin Label</title>
<link rel="stylesheet" href="https://fonts.googleapis.com/css2?family=Great+Vibes&family=Jost:wght@400;600&family=Libre+Baskerville:wght@700&display=swap">
<style>
  :root {
    --page-bg: #f3f3f4;
    --label-white: #ffffff;
    --frame-grey: #6f6f72;
    --pattern-grey: #e9e9ea;
    --teal-deep: #00AB8E;
    --teal-mid: #00BBA5;
    --teal-light: #67D7C9;
    --lime: #82FF00;
    --ink-grey: #5d5d60;
    --meta-grey: #7a7a7d;
  }
  html, body {
    margin: 0;
    padding: 0;
    width: 1200px;
    height: 1086px;
    overflow: hidden;
    background: var(--page-bg);
  }
  .label {
    display: block;
    width: 1200px;
    height: 1086px;
  }
  .label-outer { fill: var(--label-white); }
  .label-frame { fill: none; stroke: var(--frame-grey); stroke-width: 6; }
  .label-pattern { fill: var(--pattern-grey); }
  .brand-mark { fill: var(--lime); }
  .brand-name {
    font-family: "Jost", sans-serif;
    font-weight: 600;
    font-size: 72px;
    fill: var(--teal-deep);
    letter-spacing: 2px;
  }
  .brand-tagline {
    font-family: "Jost", sans-serif;
    font-weight: 600;
    font-size: 15px;
    fill: var(--teal-deep);
    letter-spacing: 1.5px;
  }
  .product-name {
    font-family: "Libre Baskerville", serif;
    font-weight: 700;
    font-size: 52px;
    fill: var(--label-white);
    letter-spacing: 3px;
  }
  .product-origin {
    font-family: "Jost", sans-serif;
    font-weight: 400;
    font-size: 20px;
    fill: var(--label-white);
    letter-spacing: 1.5px;
  }
  .blend-name {
    font-family: "Great Vibes", cursive;
    font-size: 50px;
    fill: var(--ink-grey);
  }
  .volume-info {
    font-family: "Jost", sans-serif;
    font-weight: 400;
    font-size: 20px;
    fill: var(--meta-grey);
    letter-spacing: 2px;
  }
</style>
</head>
<body>
<svg class="label" viewBox="0 0 1200 1086" xmlns="http://www.w3.org/2000/svg">
  <defs>
    <linearGradient id="band-fill" x1="0" y1="0" x2="1" y2="0">
      <stop offset="0" stop-color="var(--teal-deep)"/>
      <stop offset="0.75" stop-color="var(--teal-mid)"/>
      <stop offset="1" stop-color="var(--teal-light)"/>
    </linearGradient>
  </defs>

  <polygon class="label-outer" points="600,63 1080,543 600,1023 120,543"/>
  <polygon class="label-pattern" role="img" aria-label="Soft grey organic line pattern filling the label" points="600,103 1040,543 600,983 160,543"/>
  <polygon class="label-frame" points="600,103 1040,543 600,983 160,543"/>

  <g class="brand">
    <rect class="brand-mark" x="436" y="318" width="52" height="52" rx="8"/>
    <text class="brand-name" x="504" y="366">KIRO</text>
    <text class="brand-tagline" x="600" y="398" text-anchor="middle">KIND INVENTIVE RARE AND ORIGINAL</text>
  </g>

  <polygon class="product-band" fill="url(#band-fill)" points="207,456 993,456 1080,543 993,630 207,630 120,543"/>
  <text class="product-name" x="600" y="546" text-anchor="middle">LONDON DRY GIN</text>
  <text class="product-origin" x="600" y="596" text-anchor="middle">PRODUCED &amp; BOTTLED IN GERMANY</text>

  <text class="blend-name" x="600" y="712" text-anchor="middle">Signature Blend</text>
  <text class="volume-info" x="600" y="804" text-anchor="middle">40%vol | 700ml</text>
</svg>
</body>
</html>
```